Ridgeline Journeys business card

please see website
www.ridgelinejourneys.comau

info needed on card
Curtis Halvey
Ph
email
Adventure Riding GPS trails

please use my logo and colours off my site

Curtis Halvey
curtis@ridgelinejourneys.com

```html
<!DOCTYPE html>
<html lang="en">
<head>
<meta charset="utf-8">
<title>Ridgeline Journeys – Business Card</title>
<link href="https://fonts.googleapis.com/css2?family=Open+Sans:wght@400;600;800&display=swap" rel="stylesheet">
<style>
  :root {
    --backdrop: #2b2624;
    --card: #141414;
    --card-edge: #1d1d1d;
    --brand-yellow: #f5cc12;
    --rule-olive: #6e6a1c;
    --text-white: #f4f4f4;
    --icon-ink: #141414;
  }
  * { margin: 0; padding: 0; box-sizing: border-box; }
  html, body {
    width: 1200px; height: 844px; overflow: hidden;
    background: var(--backdrop);
    font-family: "Open Sans", Arial, sans-serif;
  }
  .canvas {
    position: relative; width: 1200px; height: 844px;
    display: flex; align-items: center; justify-content: center; gap: 40px;
  }
  .card {
    position: relative; width: 540px; height: 309px;
    background: radial-gradient(ellipse at 40% 30%, var(--card-edge), var(--card) 70%);
    box-shadow: 0 10px 30px rgba(0,0,0,.45);
    overflow: hidden;
  }

  /* brand name lockup */
  .brand {
    display: flex; align-items: center; gap: 16px;
  }
  .brand-mark {
    width: 46px; height: 46px; background: var(--brand-yellow);
  }
  .brand-name {
    color: var(--text-white); font-weight: 800; text-transform: uppercase;
    font-size: 28px; line-height: 1.02; letter-spacing: .5px;
  }

  /* front */
  .card-front .brand { position: absolute; left: 190px; top: 58px; }
  .card-front .divider {
    position: absolute; left: 0; right: 0; top: 165px; height: 1px; background: var(--rule-olive);
  }
  .contact { position: absolute; left: 34px; top: 196px; }
  .contact-name {
    color: var(--brand-yellow); font-weight: 600; font-size: 18px; margin-bottom: 10px;
    padding-bottom: 6px; border-bottom: 1px solid var(--rule-olive); width: 260px;
  }
  .contact-list { list-style: none; }
  .contact-item {
    display: flex; align-items: center; gap: 10px;
    color: var(--text-white); font-size: 14px; line-height: 23px;
  }
  .contact-icon { width: 15px; height: 15px; flex: none; }

  /* back */
  .card-back .brand { position: absolute; left: 120px; top: 82px; }
  .card-back .tagline {
    position: absolute; left: 0; right: 0; top: 178px; text-align: center;
    color: var(--brand-yellow); font-weight: 600; font-size: 15px;
  }
  .card-back .site {
    position: absolute; left: 0; right: 0; top: 208px; text-align: center;
    color: var(--text-white); font-size: 12px;
  }
</style>
</head>
<body>
<main class="canvas">

  <section class="card card-front" aria-label="Card front">
    <div class="brand">
      <span class="brand-mark"></span>
      <span class="brand-name">Ridgeline<br>Journeys</span>
    </div>
    <div class="divider"></div>
    <div class="contact">
      <p class="contact-name">Curtis Halvey</p>
      <ul class="contact-list">
        <li class="contact-item">
          <svg class="contact-icon" viewBox="0 0 16 16" aria-hidden="true"><rect width="16" height="16" rx="3" fill="#f5cc12"/><path d="M4 5.5c0-1 1-1.5 1.5-1.5h5c.5 0 1.5.5 1.5 1.5v.8H9.5v-.8h-3v.8H4zM4.5 7.5h7l.5 4.5H4z" fill="#141414"/></svg>
          (044)-318-2756
        </li>
        <li class="contact-item">
          <svg class="contact-icon" viewBox="0 0 16 16" aria-hidden="true"><rect width="16" height="16" rx="3" fill="#f5cc12"/><rect x="3.5" y="5" width="9" height="6.5" fill="#141414"/><path d="M3.5 5l4.5 3.5L12.5 5" stroke="#f5cc12" stroke-width="1" fill="none"/></svg>
          curtis@ridgelinejourneys.com
        </li>
        <li class="contact-item">
          <svg class="contact-icon" viewBox="0 0 16 16" aria-hidden="true"><rect width="16" height="16" rx="3" fill="#f5cc12"/><path d="M5 11l6-6M6.5 6.5l-1.5 1.5a2 2 0 0 0 3 3l1.5-1.5M9.5 9.5l1.5-1.5a2 2 0 0 0-3-3L6.5 6.5" stroke="#141414" stroke-width="1.4" fill="none" stroke-linecap="round"/></svg>
          www.ridgelinejourneys.comau
        </li>
      </ul>
    </div>
  </section>

  <section class="card card-back" aria-label="Card back">
    <div class="brand">
      <span class="brand-mark"></span>
      <span class="brand-name">Ridgeline<br>Journeys</span>
    </div>
    <p class="tagline">Adventure Riding GPS trails</p>
    <p class="site">www.ridgelinejourneys.comau</p>
  </section>

</main>
</body>
</html>
```